New Business Card Design Project LORVANTI-Italy

we are LORVANTI-Italy
our company in the market for 3 years we are luxury cosmetic company and its about time for a facelift :)
i will like to have elegant luxurious and unique business card
that will give the person that get it a unique, luxurious and elegant impression
I'm VERY OPEN FOR NEW IDEAS , even duo i add a few files of things that i see on line and i like them

i add my logo as well
my website is LORVANTI.COM
(if you would like to see the main style that we have)

Target Market(s)

adult that have money :)

Industry/Entity Type

Business

Contact Information for Business Card

Name - Dario Lorvanti
Position - CEO and CO Founder
address - 4817 E Halvern
telephone - 555-384-1926
email - dario@lorvanti.com
fax - 555-384-1926
website - LORVANTI.COM

Colors
000000
959595
fbee3e
ffffff

Requirements
Must have
• big logo in GOLD color
• elegant look
• impressive
Nice to have
• not must but maybe classy pattern background
• not must but maybe emblem
• maybe clear plastic business card
Should not have
• colors
• images

```html
<!DOCTYPE html>
<html lang="en">
<head>
<meta charset="utf-8">
<title>LORVANTI Italy – Business Card</title>
<link rel="stylesheet" href="https://fonts.googleapis.com/css2?family=Cinzel:wght@500&family=Josefin+Sans:wght@300;400&family=Roboto:wght@400&display=swap">
<style>
  :root {
    --backdrop: #d9dde2;
    --card: #0d0d0e;
    --card-glow: #1c1d1f;
    --gold: #d2b02c;
    --amber: #eea834;
    --ink: #0d0d0e;
  }
  * { box-sizing: border-box; margin: 0; padding: 0; }
  html, body { width: 1200px; height: 1200px; overflow: hidden; }
  body {
    background: var(--backdrop);
    position: relative;
    font-family: "Roboto", Arial, sans-serif;
  }
  .card {
    position: absolute;
    left: 170px;
    width: 860px;
    height: 490px;
    background: radial-gradient(ellipse at 50% 55%, var(--card-glow), var(--card) 70%);
    box-shadow: 0 14px 30px rgba(0,0,0,.28);
    overflow: hidden;
  }
  .card--front { top: 80px; }
  .card--back { top: 630px; }

  /* Brand lockup */
  .brand { position: absolute; text-align: center; color: var(--gold); font-family: "Cinzel", Georgia, serif; font-weight: 500; }
  .brand__mark {
    display: block; margin: 0 auto;
    border: 5px solid var(--gold); border-radius: 50%;
  }
  .brand__name { display: block; letter-spacing: 2px; line-height: 1; }
  .brand__rule { display: block; height: 4px; background: var(--gold); margin: 0 auto; }
  .brand__country { display: block; letter-spacing: 3px; line-height: 1; }

  .card--front .brand { left: 0; right: 0; top: 50px; }
  .card--front .brand__mark { width: 190px; height: 190px; }
  .card--front .brand__name { font-size: 96px; margin-top: 34px; }
  .card--front .brand__rule { width: 520px; margin-top: 14px; }
  .card--front .brand__country { font-size: 32px; margin-top: 14px; }

  /* Back side */
  .divider { position: absolute; left: 440px; top: 50px; width: 4px; height: 390px; background: var(--amber); }
  .stripe { position: absolute; top: 0; width: 16px; height: 110px; background: var(--amber); }
  .stripe--one { left: 620px; }
  .stripe--two { left: 652px; }
  .tab { position: absolute; left: 612px; top: 445px; width: 60px; height: 24px; background: var(--amber); }

  .card--back .brand { left: 460px; right: 0; top: 118px; }
  .card--back .brand__mark { width: 150px; height: 150px; border-width: 4px; }
  .card--back .brand__name { font-size: 68px; margin-top: 22px; }
  .card--back .brand__rule { width: 340px; margin-top: 10px; height: 3px; }
  .card--back .brand__country { font-size: 24px; margin-top: 10px; }

  .person { position: absolute; left: 70px; top: 55px; color: var(--gold); font-family: "Josefin Sans", Arial, sans-serif; }
  .person__name { font-size: 34px; font-weight: 400; font-variant: small-caps; letter-spacing: 1px; padding: 0 10px 6px 10px; border-bottom: 2px solid var(--gold); }
  .person__role { font-size: 15px; font-weight: 300; font-variant: small-caps; letter-spacing: 1px; margin: 6px 0 0 40px; }

  .contacts { position: absolute; left: 50px; top: 190px; list-style: none; }
  .contacts__item { display: flex; align-items: center; height: 54px; color: var(--gold); font-size: 21px; }
  .contacts__icon {
    width: 32px; height: 32px; border-radius: 5px; background: var(--amber);
    display: flex; align-items: center; justify-content: center; margin-right: 14px; flex: none;
  }
  .contacts__icon svg { width: 22px; height: 22px; fill: none; stroke: var(--ink); stroke-width: 2; stroke-linecap: round; stroke-linejoin: round; }
</style>
</head>
<body>

<section class="card card--front" aria-label="Card front">
  <div class="brand">
    <span class="brand__mark" aria-hidden="true"></span>
    <span class="brand__name">LORVANTI</span>
    <span class="brand__rule"></span>
    <span class="brand__country">ITALY</span>
  </div>
</section>

<section class="card card--back" aria-label="Card back">
  <div class="person">
    <p class="person__name">Dario Lorvanti</p>
    <p class="person__role">CEO and CO Founder</p>
  </div>

  <ul class="contacts">
    <li class="contacts__item">
      <span class="contacts__icon"><svg viewBox="0 0 24 24"><path d="M12 21s-6-6.2-6-11a6 6 0 0 1 12 0c0 4.8-6 11-6 11z"/><circle cx="12" cy="10" r="2.3"/></svg></span>
      4817 E Halvern
    </li>
    <li class="contacts__item">
      <span class="contacts__icon"><svg viewBox="0 0 24 24"><path d="M5 4h4l2 5-2.5 1.5a11 11 0 0 0 5 5L15 13l5 2v4a2 2 0 0 1-2 2A16 16 0 0 1 3 6a2 2 0 0 1 2-2z"/></svg></span>
      555-384-1926
    </li>
    <li class="contacts__item">
      <span class="contacts__icon"><svg viewBox="0 0 24 24"><rect x="3" y="6" width="18" height="12"/><path d="M3 6l9 7 9-7"/></svg></span>
      dario@lorvanti.com
    </li>
    <li class="contacts__item">
      <span class="contacts__icon"><svg viewBox="0 0 24 24"><rect x="7" y="3" width="10" height="6"/><rect x="4" y="9" width="16" height="8" rx="1"/><rect x="7" y="14" width="10" height="7"/></svg></span>
      555-384-1926
    </li>
    <li class="contacts__item">
      <span class="contacts__icon"><svg viewBox="0 0 24 24"><circle cx="12" cy="12" r="9"/><path d="M3 12h18M12 3c3 3 3 15 0 18M12 3c-3 3-3 15 0 18"/></svg></span>
      lorvanti.com
    </li>
  </ul>

  <span class="divider"></span>
  <span class="stripe stripe--one"></span>
  <span class="stripe stripe--two"></span>

  <div class="brand">
    <span class="brand__mark" aria-hidden="true"></span>
    <span class="brand__name">LORVANTI</span>
    <span class="brand__rule"></span>
    <span class="brand__country">ITALY</span>
  </div>
  <span class="tab"></span>
</section>

</body>
</html>
```